I am looking for a modern, clean and neat design for a reflexology and well being business. The business name is Gralo Tund (this is an old Latin word for wellbeing). The colours I would like are purple, white and grey. I am open to suggestions for pictures such as healing or working hands, a pair of feet, images that represent my business that you may think of....... or maybe you think no images at all would be best? My tag line is: "Relax, Renew, Revive" or "Find you balance......... Relax, Renew, Revive" I can decide which I want so I would like to see what both would look like. I would like space on the back to write the client's appointment date and time (more than once)

```html
<!DOCTYPE html>
<html lang="en">
<head>
<meta charset="utf-8">
<title>Gralo Tund – Business Card</title>
<link rel="stylesheet" href="https://fonts.googleapis.com/css2?family=Open+Sans:wght@400;600;700&display=swap">
<style>
  :root {
    --page: #2b2b2d;
    --white: #ffffff;
    --lilac: #a3bae0;
    --lilac-soft: #b7c9e8;
    --grey-dark: #4a4a4c;
    --grey-mid: #5c5c60;
    --dots: #6a6a6e;
  }
  * { box-sizing: border-box; margin: 0; padding: 0; }
  html, body {
    width: 1200px; height: 900px; overflow: hidden;
    background: var(--page);
    font-family: "Open Sans", sans-serif;
  }
  .stage { position: relative; width: 1200px; height: 900px; }
  .card {
    position: absolute; width: 560px; height: 320px;
    border-radius: 24px; overflow: hidden;
    box-shadow: 0 14px 30px rgba(0,0,0,.45);
  }

  /* Appointment side */
  .card--appointment { left: 60px; top: 110px; background: var(--white); }
  .tagline {
    position: absolute; right: 44px; top: 58px;
    font-size: 12px; font-weight: 600; letter-spacing: .5px; color: var(--grey-dark);
  }
  .brand {
    position: absolute; display: flex; align-items: center; gap: 10px;
    font-weight: 600; color: var(--grey-mid); line-height: 1.2;
  }
  .brand__dot { border-radius: 50%; background: var(--lilac); flex: none; }
  .card--appointment .brand { right: 44px; top: 88px; font-size: 22px; }
  .card--appointment .brand__dot { width: 38px; height: 38px; }
  .appointment { position: absolute; left: 40px; top: 178px; width: 370px; color: var(--grey-dark); }
  .appointment__title { font-size: 17px; font-weight: 700; margin-bottom: 8px; }
  .appointment__row { display: flex; align-items: flex-end; font-size: 13px; height: 26px; }
  .appointment__row span { flex: 1; border-bottom: 1.5px dotted var(--dots); margin-left: 4px; margin-bottom: 4px; }

  /* Contact side */
  .card--contact { left: 580px; top: 470px; background: var(--lilac); }
  .watermark {
    position: absolute; right: 60px; top: 40px;
    font-size: 28px; font-weight: 600; letter-spacing: 2px;
    color: var(--white); opacity: .18;
  }
  .brand-disc {
    position: absolute; left: -70px; top: 150px; width: 330px; height: 330px;
    border-radius: 50%; background: var(--white);
  }
  .card--contact .brand {
    left: 36px; top: 170px; flex-direction: column; align-items: flex-start; gap: 8px;
    font-size: 26px; font-weight: 400; letter-spacing: 1.5px;
  }
  .card--contact .brand__dot { width: 56px; height: 56px; margin-left: 60px; }
  .person { position: absolute; right: 40px; top: 112px; text-align: right; width: 230px; }
  .person__name { font-size: 21px; font-weight: 700; letter-spacing: 1.5px; color: var(--white); line-height: 1.3; }
  .person__role { font-size: 10px; font-weight: 600; letter-spacing: 1px; color: var(--grey-dark); padding-bottom: 4px; border-bottom: 1.5px solid var(--white); }
  .contacts-rule { position: absolute; left: 290px; top: 196px; width: 230px; border-top: 1.5px solid var(--white); }
  .contacts { position: absolute; left: 290px; top: 204px; list-style: none; }
  .contacts li { display: flex; align-items: center; gap: 8px; font-size: 13px; color: var(--white); line-height: 20px; }
  .contacts svg { width: 11px; height: 11px; fill: var(--grey-dark); flex: none; }
</style>
</head>
<body>
<div class="stage">

  <section class="card card--appointment">
    <p class="tagline">RELAX, RENEW, REVIVE</p>
    <div class="brand"><span class="brand__dot"></span>Gralo Tund</div>
    <div class="appointment">
      <p class="appointment__title">Appointment:</p>
      <p class="appointment__row">Name:<span></span></p>
      <p class="appointment__row">Time:<span></span></p>
      <p class="appointment__row">Date:<span></span></p>
    </div>
  </section>

  <section class="card card--contact">
    <p class="watermark">GRALO TUND</p>
    <div class="brand-disc"></div>
    <div class="brand"><span class="brand__dot"></span>GRALO TUND</div>
    <div class="person">
      <p class="person__name">MARA QUELL</p>
      <p class="person__role">DIRECTOR</p>
    </div>
    <div class="contacts-rule"></div>
    <ul class="contacts">
      <li><svg viewBox="0 0 12 12"><path d="M2.5 1l2 2.2-1 1.3a7 7 0 0 0 4 4l1.3-1 2.2 2-1.3 1.5C5 11 1 7 1 2.3z"/></svg>+330 5172-8394</li>
      <li><svg viewBox="0 0 12 12"><path d="M1 2.5h10v7H1zM1.8 3.2L6 6.3l4.2-3.1v.9L6 7.2 1.8 4.1z"/></svg>info@gralotund.com</li>
      <li><svg viewBox="0 0 12 12"><circle cx="6" cy="6" r="5"/></svg>www.gralotund.com</li>
    </ul>
  </section>

</div>
</body>
</html>
```